Redesign of business card for Cedar Ridge Mechanical

We are looking for a new design for our business cards for Cedar Ridge Mechanical. We are a plumbing & HVAC construction company, operating on the West Coast of Canada and USA. Logo attached.
Industry/Entity Type
Construction - Plumbing & HVAC
Contact Information for Business Card
Name, address, phone numbers, email, website address
Look and feel
Each slider illustrates characteristics of the customer's brand and the style your logo design should communicate.

```html
<!DOCTYPE html>
<html lang="en">
<head>
<meta charset="utf-8">
<title>Cedar Ridge Mechanical – Business Card</title>
<link rel="stylesheet" href="https://fonts.googleapis.com/css2?family=Montserrat:wght@400;500;600;700&display=swap">
<style>
  :root {
    --backdrop: #8a7a66;
    --card-light: #ffffff;
    --card-dark: #2b2b2b;
    --ink: #231f20;
    --band-dark: #231f20;
    --band-grey: #5f5f61;
    --paper-text: #ffffff;
  }
  * { margin: 0; padding: 0; box-sizing: border-box; }
  html, body { width: 900px; height: 1200px; overflow: hidden; }
  body {
    background: var(--backdrop);
    font-family: "Montserrat", Arial, sans-serif;
    color: var(--ink);
    position: relative;
  }
  .card {
    position: absolute;
    width: 742px;
    height: 440px;
    border-radius: 22px;
    overflow: hidden;
    box-shadow: 0 8px 24px rgba(0,0,0,0.35);
  }
  .card--front { left: 80px; top: 131px; background: var(--card-light); }
  .card--back { left: 79px; top: 638px; background: var(--card-dark); }

  .brand {
    position: absolute;
    display: flex;
    align-items: center;
    font-weight: 700;
    text-transform: uppercase;
    line-height: 1.1;
  }
  .brand__mark { flex: none; }
  .card--front .brand {
    left: 108px; top: 160px; width: 230px;
    gap: 12px; font-size: 21px; color: var(--ink);
  }
  .card--front .brand__mark { width: 22px; height: 22px; background: var(--ink); }
  .card--back .brand {
    left: 0; right: 0; top: 170px;
    justify-content: center; gap: 20px;
    font-size: 40px; color: var(--paper-text);
  }
  .card--back .brand__mark { width: 36px; height: 36px; background: var(--paper-text); }

  .divider {
    position: absolute;
    left: 349px; top: 112px;
    width: 2px; height: 204px;
    background: var(--ink);
  }
  .contact { position: absolute; left: 368px; top: 108px; }
  .contact__name { font-size: 26px; font-weight: 700; line-height: 1.2; }
  .contact__role { font-size: 16px; font-weight: 500; margin-top: 2px; }
  .contact__address { font-size: 16px; line-height: 20px; margin-top: 20px; }
  .contact__list { list-style: none; margin-top: 18px; }
  .contact__item {
    display: flex; align-items: center; gap: 10px;
    font-size: 15.5px; height: 30px;
  }
  .contact__icon { width: 17px; height: 17px; flex: none; }

  .bands { position: absolute; left: 0; top: 392px; width: 742px; height: 25px; }
</style>
</head>
<body>

<section class="card card--front" aria-label="Business card front">
  <div class="brand">
    <span class="brand__mark"></span>
    <span class="brand__name">Cedar Ridge Mechanical</span>
  </div>

  <div class="divider"></div>

  <div class="contact">
    <h1 class="contact__name">Dana Whitfield</h1>
    <p class="contact__role">Managing Director</p>
    <p class="contact__address">48 Harbor Pine Road<br>Bellingham, WA 98225</p>
    <ul class="contact__list">
      <li class="contact__item">
        <svg class="contact__icon" viewBox="0 0 24 24" aria-hidden="true">
          <path fill="#231f20" d="M6.6 10.8a15.1 15.1 0 0 0 6.6 6.6l2.2-2.2a1 1 0 0 1 1-.25 11.4 11.4 0 0 0 3.6.57 1 1 0 0 1 1 1V20a1 1 0 0 1-1 1A17 17 0 0 1 3 4a1 1 0 0 1 1-1h3.5a1 1 0 0 1 1 1c0 1.25.2 2.45.57 3.57a1 1 0 0 1-.25 1z"/>
        </svg>
        <span>360.555.0142</span>
      </li>
      <li class="contact__item">
        <svg class="contact__icon" viewBox="0 0 24 24" aria-hidden="true">
          <path fill="#231f20" d="M3 6h18v12H3z"/>
          <path fill="none" stroke="#fff" stroke-width="1.6" d="M3.5 6.5 12 13l8.5-6.5"/>
        </svg>
        <span>info@cedarridgemechanical.com</span>
      </li>
      <li class="contact__item">
        <svg class="contact__icon" viewBox="0 0 24 24" aria-hidden="true">
          <circle cx="12" cy="12" r="9" fill="none" stroke="#231f20" stroke-width="2"/>
          <path fill="none" stroke="#231f20" stroke-width="1.6" d="M3 12h18M12 3c3 3.5 3 14.5 0 18M12 3c-3 3.5-3 14.5 0 18"/>
        </svg>
        <span>www.cedarridgemechanical.com</span>
      </li>
    </ul>
  </div>

  <svg class="bands" viewBox="0 0 742 25" aria-hidden="true">
    <polygon points="0,0 548,0 520,25 0,25" fill="var(--band-dark)"/>
    <polygon points="558,0 742,0 742,25 532,25" fill="var(--band-grey)"/>
  </svg>
</section>

<section class="card card--back" aria-label="Business card back">
  <div class="brand">
    <span class="brand__mark"></span>
    <span class="brand__name">Cedar Ridge Mechanical</span>
  </div>
</section>

</body>
</html>
```